Verdel Harvest - Stationery Design Project

We need a stationary for our business. We grow roots and fruits in Central and South America, we import and distribute in FL, USA. We do fresh and frozen products.

Target Market(s)

Small and big supermarkets, wholesalers, traders, distributors, etc

Industry/Entity Type

Business

```html
<!DOCTYPE html>
<html lang="en">
<head>
<meta charset="utf-8">
<title>Verdel Harvest – Stationery</title>
<link href="https://fonts.googleapis.com/css2?family=Montserrat:wght@400;500&display=swap" rel="stylesheet">
<style>
  :root{
    --backdrop:#e5e5e3;
    --slate:#535f67;
    --paper:#f9f9f9;
    --brand:#e3820f;
    --muted:#6f7478;
    --leaf-tint:#ecece6;
    --leaf-clear:rgba(236,236,230,0);
  }
  html,body{margin:0;padding:0;overflow:hidden}
  body{width:1200px;height:1000px;background:var(--backdrop);position:relative;font-family:"Montserrat",Arial,sans-serif}
  .piece{position:absolute;overflow:hidden}
  .wordmark{position:absolute;color:var(--brand);font-weight:500;white-space:nowrap;letter-spacing:.01em;text-transform:uppercase;line-height:1}
  .mark-dot{position:absolute;background:var(--brand);border-radius:50%}

  /* folder */
  .folder{left:190px;top:108px;width:385px;height:542px;background:var(--slate)}
  .folder .wordmark{left:0;width:385px;text-align:center;top:106px;font-size:34px}
  .folder .mark-dot{left:184px;top:70px;width:18px;height:18px}

  /* letterhead */
  .letterhead{left:610px;top:122px;width:375px;height:528px;background:var(--paper)}
  .letterhead .wordmark{left:21px;top:39px;font-size:15px}
  .letterhead .mark-dot{left:93px;top:24px;width:9px;height:9px}
  .contact-list{position:absolute;left:241px;top:31px;margin:0;padding:0;list-style:none;font-size:7px;color:var(--muted)}
  .contact-list li{display:flex;align-items:center;height:11.5px}
  .contact-list li::before{content:"";width:6px;height:6px;border-radius:50%;background:#8c9a6a;margin-right:13px}
  .side-tab{position:absolute;right:0;top:20px;width:13px;height:43px;background:var(--slate)}
  .foot-band{position:absolute;left:0;right:0;bottom:0;height:19px;background:var(--slate)}
  .decor-area{position:absolute;background:radial-gradient(ellipse closest-side at 50% 50%,var(--leaf-tint) 0%,var(--leaf-tint) 55%,var(--leaf-clear) 100%)}
  .letterhead .decor-area{left:-40px;top:243px;width:455px;height:310px}

  /* envelope */
  .envelope{left:190px;top:698px;width:392px;height:192px;background:var(--paper)}
  .flap{position:absolute;left:0;top:0;width:392px;height:57px}
  .envelope .wordmark{left:0;width:392px;text-align:center;top:25px;font-size:11px}
  .envelope .mark-dot{left:193px;top:15px;width:6px;height:6px}

  /* compliment card */
  .card{left:618px;top:698px;width:392px;height:192px;background:var(--paper)}
  .card .wordmark{left:23px;top:25px;font-size:11px}
  .card .mark-dot{left:75px;top:15px;width:6px;height:6px}
  .card .decor-area{left:110px;top:-20px;width:330px;height:210px}
</style>
</head>
<body>

<section class="piece folder">
  <span class="mark-dot"></span>
  <div class="wordmark">Verdel Harvest</div>
</section>

<section class="piece letterhead">
  <div class="decor-area" role="img" aria-label="Large faint brand leaf motif in pale grey"></div>
  <span class="mark-dot"></span>
  <div class="wordmark">Verdel Harvest</div>
  <ul class="contact-list">
    <li>0407 552 918</li>
    <li>support@verdelharvest.com</li>
    <li>www.verdelharvest.com</li>
  </ul>
  <div class="side-tab"></div>
  <div class="foot-band"></div>
</section>

<section class="piece envelope">
  <svg class="flap" viewBox="0 0 392 57" aria-hidden="true">
    <path d="M0 0H392V35Q392 57 370 57H22Q0 57 0 35Z" fill="var(--slate)"/>
  </svg>
  <span class="mark-dot"></span>
  <div class="wordmark">Verdel Harvest</div>
</section>

<section class="piece card">
  <div class="decor-area" role="img" aria-label="Large faint brand leaf motif in pale grey"></div>
  <span class="mark-dot"></span>
  <div class="wordmark">Verdel Harvest</div>
  <div class="foot-band"></div>
</section>

</body>
</html>
```